Valdane Companies Business Card Design

We need a new business card for our Private Equity Real Estate Development firm, “Valdane” and our EB-5 regional center “Thornmere Regional Center” on one card. We prefer a design that is simple, elegant, and represents the luxury products we design and build as well as the financial security and stability our successful history has produced. We are an industry leader in our field and 3rd generation family business that has evolved into an institutional quality investment platform. Considered design size is standard business card dimensions (3.5 x 2 inches with an additional 1/8 inch space for design elements or backgrounds that extend beyond the finished size of your piece.

Target Market(s)

• High net worth individuals
• Highly skilled technical workers and physicians in the US seeking investment-based immigration opportunities
• Sophisticated private equity investors
• Intermediary partners include domestic attorneys and investment brokers, as well as international agent networks
• US real estate developers

Industry/Entity Type

Finance

Contact Information for Business Card

(Providing placeholder info for personal information, please design for longer character spaces, longer names and addresses etc..)
• Logo for Valdane
• Logo for Thornmere Regional Center
• Full name: Marcus Valdane
• Job title: CEO
• Email address: mvaldane@valdanecompanies.com
• Cell phone number: +1.555.314.2287
• Office number +1.555.628.4410
• Office address: Larkfield Court 5, 4817 Vista Orilla, Cedar Vale, CA.
• Website: www.valdanecompanies.com

Font styles to use
Serif
Sans Serif

Colors
ec1f27
ffffff
000000

Requirements
Must have
• • Logo for Valdane
• • Logo for Thornmere Regional Center
• - Use rounded corners
• (See .ai file included for logos)
Nice to have
• • Simple, elegant design
• • Aesthetically compatible with our website design (www.valdanecompanies.com)
• • Color palette including but not limited to white, black, and red (as per logos)
Should not have
• - Not too much red color
• - Do not stack both logos on top of each other

```html
<!DOCTYPE html>
<html lang="en">
<head>
<meta charset="utf-8">
<title>Valdane Companies Business Card</title>
<link rel="stylesheet" href="https://fonts.googleapis.com/css2?family=Libre+Baskerville:wght@400;700&family=Roboto:wght@400;500&display=swap">
<style>
  :root {
    --stage: #2a2a2a;
    --card-white: #f3f3f3;
    --crimson: #8e1238;
    --crimson-deep: #6e0c2a;
    --crimson-bright: #b81d4f;
    --ink: #111111;
    --body-grey: #555555;
    --white: #ffffff;
  }
  * { margin: 0; padding: 0; box-sizing: border-box; }
  html, body { width: 1200px; height: 960px; overflow: hidden; }
  body { background: var(--stage); position: relative; font-family: "Roboto", Arial, sans-serif; }

  .card { position: absolute; width: 600px; height: 343px; border-radius: 3px; overflow: hidden; }

  .card-front { left: 314px; top: 113px; background: var(--card-white); }
  .front-logo { position: absolute; left: 42px; top: 50px; display: flex; align-items: center; gap: 30px; }
  .front-logo .mark { width: 64px; height: 64px; background: var(--crimson); flex: none; }
  .front-logo .wordmark {
    font-family: "Libre Baskerville", Georgia, serif; font-weight: 700;
    color: var(--crimson); text-transform: uppercase; line-height: 1;
  }
  .front-logo .name { display: block; font-size: 31px; letter-spacing: 0.3px; }
  .front-logo .sub { display: block; font-size: 10px; letter-spacing: 4.6px; margin-top: 7px; padding-left: 5px; }

  .holder { position: absolute; left: 44px; top: 152px; }
  .holder-name {
    font-family: "Libre Baskerville", Georgia, serif; font-weight: 700; font-size: 21px;
    color: var(--crimson); text-transform: uppercase; line-height: 1.1;
  }
  .holder-title { font-family: "Libre Baskerville", Georgia, serif; font-size: 14px; color: var(--ink); margin-top: 2px; }
  .address { position: absolute; left: 44px; top: 202px; font-size: 14.5px; line-height: 18px; color: var(--body-grey); }
  .contact { position: absolute; left: 44px; top: 265px; font-size: 14.5px; line-height: 19px; color: var(--body-grey); }
  .contact .label { color: var(--crimson); font-weight: 500; }
  .web-band {
    position: absolute; right: 0; top: 0; width: 47px; height: 100%;
    background: linear-gradient(180deg, var(--crimson-deep), var(--crimson-bright) 50%, var(--crimson-deep));
  }
  .web-band .url {
    position: absolute; left: 50%; top: 50%; transform: translate(-50%, -50%) rotate(90deg);
    color: var(--white); font-size: 13.5px; letter-spacing: 1.4px; white-space: nowrap;
  }

  .card-back {
    left: 311px; top: 472px;
    background: radial-gradient(ellipse at 50% 40%, var(--crimson-bright) 0%, var(--crimson) 55%, var(--crimson-deep) 100%);
  }
  .back-logo { position: absolute; left: 0; right: 0; top: 190px; text-align: center; color: var(--white); }
  .back-logo .name {
    font-family: "Libre Baskerville", Georgia, serif; font-weight: 700; font-size: 40px;
    text-transform: uppercase; letter-spacing: 1px; line-height: 1;
  }
  .back-logo .tag {
    font-family: "Roboto", Arial, sans-serif; font-size: 14px; letter-spacing: 4.5px;
    text-transform: uppercase; margin-top: 9px;
  }
</style>
</head>
<body>
  <section class="card card-front">
    <div class="front-logo">
      <span class="mark"></span>
      <span class="wordmark">
        <span class="name">Thornmere</span>
        <span class="sub">Regional Center</span>
      </span>
    </div>
    <div class="holder">
      <div class="holder-name">Marcus Valdane</div>
      <div class="holder-title">CEO</div>
    </div>
    <div class="address">
      Larkfield Court 5<br>
      4817 Vista Orilla<br>
      Cedar Vale, CA.
    </div>
    <div class="contact">
      <span class="label">Phone:</span> +1.555.628.4410&nbsp; <span class="label">Cell:</span> +1.555.314.2287<br>
      mvaldane@valdanecompanies.com
    </div>
    <div class="web-band"><span class="url">www.valdanecompanies.com</span></div>
  </section>

  <section class="card card-back">
    <div class="back-logo">
      <div class="name">Valdane</div>
      <div class="tag">Capital</div>
    </div>
  </section>
</body>
</html>
```